KorvaNest - Home Income and Business Resources Platform

I am looking for a website template for a multi-purposed website. This website will feature:

1.) Website Directory with Ratings & comments on listings
2.) Company Blog
3.) Homepage with Content (see files for homepage mock)

I would like the Design to have a default width 1170px (wider then normal)

Of course I am looking for Pages for Listings to be designed.

Great looking BLOG Layout: http://journal.plimworks.example/html/blog.html

I would like 4 Versions of a Website Directory Listing "Box"
1.) Basic Listing Box
2.) Sponsored Listing Box
3.) Recommended Listing Box
4.) Stay Away From Listing Box

Information on the Listing Page (Like on a Category Page)
Site Name, Site URL, Website Image, # of Views, Rating and # of Comments

Information on the Listing Details Page:
Same as ABOVE + About website Description, Vornic Score, Category Information

Decent looking examples is here: https://samples.trevolin.example/directory/computers/ and http://www.zqrankhub.example/.

I will include some sketches and screenshots of things I like/looking for. As designers,you have creative freedom and are encouraged to show this. This is Phase one of this project and winning designer is guaranteed to have future work for this project.

Target Market(s)

Directory, business, websites

Industry/Entity Type

Business

Coding

Coded - Design and coding required

Number of Pages Required

5+ page

Font styles to use
Sans Serif

Colors

Designer to choose colors to be used in the design.

Requirements
Must have
• Professional yet clean look. The use of Icons & images
• Unique Look
Should not have
• Any exact copies of any examples I provided

```html
<!DOCTYPE html>
<html lang="en">
<head>
<meta charset="utf-8">
<title>KorvaNest – About</title>
<link href="https://fonts.googleapis.com/css2?family=Raleway:wght@300;400;500;600;700&family=Lato:wght@300;400;700&display=swap" rel="stylesheet">
<style>
:root{
  --page-bg:#e9f1fb;
  --blue:#0f6bd0;
  --orange:#f7720f;
  --ink:#2a2a2a;
  --text:#3d3d3d;
  --line:#d7dee8;
  --white:#ffffff;
  --card-border:#9cc0ea;
}
*{box-sizing:border-box;margin:0;padding:0}
html,body{width:880px;height:1200px;overflow:hidden}
body{background:var(--page-bg);font-family:"Lato",sans-serif;color:var(--text);position:relative}
a{text-decoration:none;color:inherit}

.site-header{position:absolute;left:32px;top:10px;width:816px;height:26px}
.brand{display:flex;align-items:center;gap:7px}
.brand-dot{width:10px;height:10px;border-radius:50%;background:var(--blue);flex:none}
.brand-name{font-family:"Lato",sans-serif;font-weight:700;font-size:14px;color:var(--ink);line-height:1}
.brand-tag{font-size:6.5px;color:var(--ink);margin-top:2px}
.phone{position:absolute;right:0;top:6px;font-size:10.5px;color:#555;display:flex;align-items:center;gap:3px}

.main-nav{position:absolute;left:32px;top:41px;width:816px;height:26px;background:var(--blue);display:flex;align-items:center}
.main-nav a{font-family:"Raleway",sans-serif;font-weight:700;font-size:10px;color:var(--white);height:26px;line-height:26px;padding:0 7px}
.main-nav a.active{background:var(--orange)}
.nav-social{margin-left:auto;display:flex;gap:8px;padding-right:10px}
.nav-social span{width:8px;height:8px;background:var(--white);display:block}

.hero{position:absolute;left:42px;top:92px;width:498px;height:177px;background:linear-gradient(120deg,#c9c3b7 0%,#ebe6dc 40%,#a4b2bd 75%,#56646e 100%)}
.about{position:absolute;left:42px;top:292px;width:500px}
.about h1{font-family:"Raleway",sans-serif;font-weight:400;font-size:29px;color:var(--ink);margin-bottom:9px}
.about p{font-size:10.6px;line-height:20.2px;color:var(--text)}

.sidebar{position:absolute;left:568px;top:91px;width:279px;height:656px;background:var(--white)}
.widget-title{font-family:"Raleway",sans-serif;font-weight:500;font-size:16px;color:var(--blue);text-align:center;padding-bottom:8px;border-bottom:1px solid var(--line)}
.social-row{display:flex;justify-content:center;gap:15px;margin-top:30px}
.social-row span{width:22px;height:22px;background:var(--blue);position:relative;display:block}
.social-row span::after{content:"";position:absolute;left:7px;bottom:-9px;border:4px solid transparent;border-top-color:var(--blue)}
.follow{font-size:9px;text-align:center;margin:8px 0 20px;color:var(--ink);padding-right:40px}
.post-img{width:254px;height:87px;margin:20px auto 0;background:linear-gradient(100deg,#6c8a3b,#b7a15e 55%,#d9b49a)}
.post-title{font-family:"Raleway",sans-serif;font-weight:700;font-size:10.3px;color:var(--blue);text-align:center;margin-top:11px}
.post-rule{width:36px;height:1px;background:#555;margin:5px auto}
.post-date{font-size:9.5px;text-align:center;color:var(--ink)}
.pager{display:flex;justify-content:center;gap:2px;margin-top:15px}
.pager span{width:17px;height:18px;background:var(--orange);display:flex;align-items:center;justify-content:center}
.ad{width:251px;height:213px;margin:16px auto 0;background:radial-gradient(circle at 40% 75%,#3a3a3a,#0c0c0c 70%);padding:16px 11px;color:var(--white)}
.ad h3{font-family:"Raleway",sans-serif;font-weight:300;font-size:35px;line-height:38px;margin-bottom:12px}
.ad p{font-size:10.3px;line-height:14.5px;text-align:justify}

.card{position:absolute;top:781px;width:257px;height:354px;background:#f7f9fc;border:1px solid var(--card-border)}
.card-icon{position:absolute;left:85px;top:-2px;width:86px;height:78px;border-radius:0 0 43px 43px;background:#ececec;box-shadow:0 3px 5px rgba(0,0,0,.12);display:flex;align-items:center;justify-content:center}
.card-icon span{width:40px;height:40px;border-radius:50%;background:linear-gradient(135deg,#f5a623,#2f6fb5)}
.card h2{position:absolute;left:10px;top:99px;font-family:"Raleway",sans-serif;font-weight:500;font-size:14px;color:var(--blue)}
.card p{position:absolute;left:10px;top:124px;width:233px;font-size:9.7px;line-height:16.8px;text-align:justify;color:#555}
.card .btn{position:absolute;left:10px;top:286px;width:114px;height:29px;line-height:29px;text-align:center;color:var(--white);font-size:10.5px;background:var(--orange)}
.card .btn.blue{background:var(--blue)}
.card-net{position:absolute;left:0;bottom:0;width:100%;height:110px;background:linear-gradient(to top,rgba(156,192,234,.25),rgba(156,192,234,0))}

.site-footer{position:absolute;left:0;top:1168px;width:880px;border-top:1px solid var(--blue);height:32px;display:flex;align-items:center;padding:0 32px;font-size:9px;color:#666}
.foot-social{display:flex;gap:6px;margin-right:20px}
.foot-social span{width:7px;height:7px;background:#666;display:block}
.foot-links{display:flex;gap:10px}
.copy{margin-left:auto}
</style>
</head>
<body>
<header class="site-header">
  <div class="brand">
    <span class="brand-dot"></span>
    <div><div class="brand-name">KorvaNest</div><div class="brand-tag">Home Income and Business Resources</div></div>
  </div>
  <div class="phone">
    <svg width="8" height="8" viewBox="0 0 10 10"><path d="M2 0l2 2-1 1.5c.6 1.4 1.6 2.4 3 3L7.5 6 10 8l-1.5 2C4 9.5.5 6 0 1.5z" fill="#0f6bd0"/></svg>
    0800-000-000-000
  </div>
</header>

<nav class="main-nav">
  <a href="#">HOME</a><a href="#" class="active">ABOUT</a><a href="#">LISTING</a><a href="#">LISTING DETAILS</a><a href="#">CONTACT</a>
  <div class="nav-social"><span></span><span></span><span></span></div>
</nav>

<div class="hero" role="img" aria-label="Photo of a folded business newspaper with market charts"></div>

<section class="about">
  <h1>About us</h1>
  <p>Lorem Ipsum is simply dummy text of the printing and typesetting industry. Lorem Ipsum has been the industry's standard dummy text ever since the 1500s, when an unknown printer took a galley of type and scrambled it to make a type specimen book. It has survived not only five centuries, but also the leap into electronic typesetting, remaining essentially unchanged. It was popularised in the 1960s with the release of Tessaline sheets containing Lorem Ipsum passages, and more recently with desktop publishing software like Quillmark Composer including versions of Lorem Ipsum. Lorem Ipsum is simply dummy text of the printing and typesetting industry. Lorem Ipsum has been the industry's standard dummy text ever since the 1500s, when an unknown printer took a galley of type and scrambled it to make a type specimen book. It has survived not only five centuries, but also the leap into electronic typesetting, remaining essentially unchanged. It was popularised in the 1960s with the release of Tessaline sheets containing Lorem Ipsum passages, and more recently with desktop publishing software like Quillmark Composer including versions of Lorem Ipsum. Lorem Ipsum is simply dummy text of the printing and typesetting industry. Lorem Ipsum has been the industry's standard dummy text ever since the 1500s, when an unknown printer took a galley of type and scrambled it to make a type specimen book. It has survived not only five centuries, but also the leap into electronic typesetting, remaining essentially unchanged. It was popularised in the 1960s with the release of Tessaline sheets containing Lorem Ipsum passages, and more recently with desktop publishing software like Quillmark Composer including versions of Lorem Ipsum.</p>
</section>

<aside class="sidebar">
  <h3 class="widget-title" style="margin-top:15px">Social Media</h3>
  <div class="social-row"><span></span><span></span><span></span><span></span><span></span></div>
  <div class="follow">Follow Us</div>
  <h3 class="widget-title">Recent Posts</h3>
  <div class="post-img" role="img" aria-label="Photo of a person relaxing outdoors on the grass"></div>
  <div class="post-title">Regular Exercise is a Natural Anti-Inflammatory</div>
  <div class="post-rule"></div>
  <div class="post-date">August 22, 2016</div>
  <div class="pager">
    <span><svg width="6" height="9" viewBox="0 0 6 9"><path d="M5 1L1.5 4.5 5 8" stroke="#fff" stroke-width="1.3" fill="none"/></svg></span>
    <span><svg width="6" height="9" viewBox="0 0 6 9"><path d="M1 1l3.5 3.5L1 8" stroke="#fff" stroke-width="1.3" fill="none"/></svg></span>
  </div>
  <h3 class="widget-title" style="margin-top:22px">Hey Warriors, We Support You!</h3>
  <div class="ad" role="img" aria-label="Dark promotional banner about advertising benefits">
    <h3>Advertising Benefits</h3>
    <p>Action plan chronic chronic illness chronic illness pain chronic pain coping with a chronic illness depression employment energy failure fibro fibro-myalgia focus food diary functional medicine goal action plan goals inflammation invisible illness job job hunting life goals</p>
  </div>
</aside>

<article class="card" style="left:31px">
  <div class="card-net"></div>
  <div class="card-icon"><span role="img" aria-label="Icon of a hand holding a house"></span></div>
  <h2>Home Income Resource Directory</h2>
  <p>Text: Find what you need, when you need it.The KorvaNest website directory is your one-stop pit for anything involved in making money from home marketing your business or finding a opportunity. Our modern, community supported directory will help a sensibl Lorem Ipsum is simply dummy text of the printing and typesettin industry. Lorem Ipsum has been the industry's standard dummy text ever since the 1500s, when an unknown printer took a</p>
  <a href="#" class="btn">Read More</a>
</article>
<article class="card" style="left:311px">
  <div class="card-net"></div>
  <div class="card-icon"><span role="img" aria-label="Icon of a presentation board with a rising bar chart"></span></div>
  <h2 style="left:15px">Advertising Benefits</h2>
  <p style="left:15px">Text: Everyone needs to advertise and we know just how to get your offer out to the right people. We have many methods including: Text ads, E-mail, Display, newsletter and even some old school methods available to make your next campaign a success. Advertise a website, a link text, full page circular or a small account manager that will handle everything Lorem Ipsum is simply dummy text of the printing and typesetting industry. dummy text ever</p>
  <a href="#" class="btn blue" style="left:15px">Read More</a>
</article>
<article class="card" style="left:590px">
  <div class="card-net"></div>
  <div class="card-icon"><span role="img" aria-label="Icon of a hand holding a coin"></span></div>
  <h2 style="left:16px">Earning With KorvaNest</h2>
  <p style="left:16px">Text: Join KorvaNest and start earning money. When you share KorvaNest and lock in an advertiser or premium listing, we reward you. Build a downline at any of our listed sites when you share KorvaNest with NO extra work. Its all done for you.We also offer a of our is the printing and typesetting industry. Lorem Ipsum has been the industry's standard dummy text ever since the 1500s, when an unknown printer took a galley esetting industry. Lorem</p>
  <a href="#" class="btn" style="left:16px">Read More</a>
</article>

<footer class="site-footer">
  <div class="foot-social"><span></span><span></span><span></span></div>
  <div class="foot-links"><a href="#">About Us</a><a href="#">Privacy Policy</a><a href="#">Terms of Use</a><a href="#">Advertise Us</a><a href="#">Help</a></div>
  <div class="copy">© 2017 Copyright</div>
</footer>
</body>
</html>
```